Real Estate Brokerage Stationery Designs

I am looking to have presentation folders with business card slots on both sides along with pockets on both sides. I've attached logos, website colors along with current business card designs.

I am looking for envelope designs both big and small. Possibly new business card designs, notepad templates for big and small notepads. Letterhead designs. Pop socket designs. Realtors name badge designs.

www.brightholdrealty.example

```html
<!DOCTYPE html>
<html lang="en">
<head>
<meta charset="utf-8">
<title>Brighthold Realty Letterhead</title>
<link rel="stylesheet" href="https://fonts.googleapis.com/css2?family=Arimo:wght@400;700&display=swap">
<style>
  :root {
    --backdrop: #a6c9ec;
    --paper: #ffffff;
    --brand-blue: #1f62b8;
    --wedge-blue: #2a86cb;
    --stripe-light: #d7dadd;
    --stripe-mid: #b4b8bc;
    --body-grey: #77797c;
    --rule-grey: #9a9da0;
  }
  * { box-sizing: border-box; margin: 0; padding: 0; }
  html, body { width: 1200px; height: 784px; overflow: hidden; }
  body {
    background: var(--backdrop);
    font-family: "Arimo", Arial, sans-serif;
    position: relative;
  }
  .letterhead {
    position: absolute;
    left: 335px; top: 17px;
    width: 530px; height: 750px;
    background: var(--paper);
    box-shadow: 0 6px 18px rgba(40, 80, 130, 0.25);
    overflow: hidden;
  }
  .corner-art { position: absolute; inset: 0; }
  .brand {
    position: absolute;
    left: 78px; top: 52px;
    display: flex; align-items: center; gap: 10px;
  }
  .brand-mark { width: 22px; height: 22px; background: var(--brand-blue); }
  .brand-name {
    font-size: 22px; font-weight: 700; color: var(--brand-blue);
    letter-spacing: 0.3px;
  }
  .letter-body {
    position: absolute;
    left: 78px; top: 108px;
    width: 380px;
    color: var(--body-grey);
    font-size: 10.2px; line-height: 14.5px;
  }
  .letter-body p + p { margin-top: 14px; }
  .signature {
    position: absolute;
    left: 120px; top: 540px;
    width: 170px; height: 56px;
    background: linear-gradient(90deg, rgba(150,150,150,0.08), rgba(150,150,150,0.18), rgba(150,150,150,0.08));
    border-radius: 4px;
  }
  .contact-footer {
    position: absolute;
    left: 0; right: 0; bottom: 32px;
    text-align: center;
  }
  .footer-rule-row {
    display: flex; align-items: center; justify-content: center; gap: 10px;
  }
  .footer-rule { width: 70px; height: 1px; background: var(--rule-grey); }
  .icon-row { display: flex; gap: 6px; }
  .icon-row svg { width: 14px; height: 14px; }
  .footer-address {
    margin-top: 7px;
    font-size: 9px; font-weight: 700; color: var(--brand-blue);
  }
  .footer-lines {
    margin-top: 4px;
    font-size: 8px; color: var(--body-grey);
  }
  .footer-lines span + span::before { content: " | "; color: var(--rule-grey); }
</style>
</head>
<body>
  <main class="letterhead">
    <svg class="corner-art" viewBox="0 0 530 750" aria-hidden="true">
      <polygon points="530,120 530,330 470,225" fill="var(--wedge-blue)"/>
      <polyline points="530,100 458,225 530,350" fill="none" stroke="var(--stripe-mid)" stroke-width="5"/>
      <polyline points="530,86 448,225 530,364" fill="none" stroke="var(--stripe-light)" stroke-width="5"/>
      <polygon points="0,440 0,690 70,565" fill="var(--wedge-blue)"/>
      <polyline points="0,418 82,565 0,712" fill="none" stroke="var(--stripe-mid)" stroke-width="5"/>
      <polyline points="0,402 93,565 0,728" fill="none" stroke="var(--stripe-light)" stroke-width="5"/>
    </svg>

    <header class="brand">
      <span class="brand-mark"></span>
      <span class="brand-name">Brighthold Realty</span>
    </header>

    <section class="letter-body">
      <p>Lorem Ipsum is simply dummy text of the printing and typesetting industry. Lorem Ipsum has been the industry's standard dummy text ever since the 1500s, when an unknown printer took a galley of type and scrambled it to make a type specimen book. It has survived not only five centuries, but also the leap into electronic typesetting, remaining essentially unchanged. It was popularised in the 1960s with the release of transfer lettering sheets containing Lorem Ipsum passages, and more recently with page layout software including versions of Lorem Ipsum.</p>
      <p>It is a long established fact that a reader will be distracted by the readable content of a page when looking at its layout. The point of using Lorem Ipsum is that it has a more-or-less normal distribution of letters, as opposed to using 'Content here, content here', making it look like readable English. Many desktop publishing packages and web page editors now use Lorem Ipsum as their default model text, and a search for 'lorem ipsum' will uncover many web sites still in their infancy. Various versions have evolved over the years, sometimes by accident, sometimes on purpose (injected humour and the like).</p>
      <p>Contrary to popular belief, Lorem Ipsum is not simply random text. It has roots in a piece of classical Latin literature from 45 BC, making it over 2000 years old. One scholar, a Latin professor at a small coastal college, looked up one of the more obscure Latin words, consectetur, from a Lorem Ipsum passage, and going through the cites of the word in classical literature, discovered the undoubtable source. Lorem Ipsum comes from two short sections of an old essay on ethics, with structures used to generate Lorem Ipsum which looks reasonable. The generated Lorem Ipsum is therefore always free from repetition, injected humour, or non-characteristic words etc.</p>
    </section>

    <div class="signature" role="img" aria-label="Handwritten signature of the sender"></div>

    <footer class="contact-footer">
      <div class="footer-rule-row">
        <span class="footer-rule"></span>
        <div class="icon-row">
          <svg viewBox="0 0 14 14"><circle cx="7" cy="7" r="7" fill="var(--brand-blue)"/><path d="M7 3.2a2.6 2.6 0 0 1 2.6 2.6C9.6 7.8 7 10.8 7 10.8S4.4 7.8 4.4 5.8A2.6 2.6 0 0 1 7 3.2z" fill="#fff"/><circle cx="7" cy="5.8" r="0.9" fill="var(--brand-blue)"/></svg>
          <svg viewBox="0 0 14 14"><circle cx="7" cy="7" r="7" fill="var(--brand-blue)"/><path d="M4.6 3.6l1.5-.3.7 2-1 .7a5 5 0 0 0 2.2 2.2l.7-1 2 .7-.3 1.5c-3.4.2-6-2.4-5.8-5.8z" fill="#fff"/></svg>
          <svg viewBox="0 0 14 14"><circle cx="7" cy="7" r="7" fill="var(--brand-blue)"/><rect x="3.6" y="4.6" width="6.8" height="4.8" fill="#fff"/><path d="M3.6 4.6L7 7.3l3.4-2.7" fill="none" stroke="var(--brand-blue)" stroke-width="0.8"/></svg>
          <svg viewBox="0 0 14 14"><circle cx="7" cy="7" r="7" fill="var(--brand-blue)"/><circle cx="7" cy="7" r="3.6" fill="none" stroke="#fff" stroke-width="0.8"/><path d="M3.4 7h7.2M7 3.4c-1.6 2-1.6 5.2 0 7.2M7 3.4c1.6 2 1.6 5.2 0 7.2" fill="none" stroke="#fff" stroke-width="0.7"/></svg>
          <svg viewBox="0 0 14 14"><circle cx="7" cy="7" r="7" fill="var(--brand-blue)"/><circle cx="7" cy="7" r="3.4" fill="#fff"/><circle cx="7" cy="7" r="2.2" fill="var(--brand-blue)"/></svg>
        </div>
        <span class="footer-rule"></span>
      </div>
      <p class="footer-address">800 Harbor Point Dr, Ste 120, Lakeview, FL 30000</p>
      <p class="footer-lines"><span>555-014-2270</span><span>555-018-3391</span><span>contact@brightholdrealty.example</span><span>www.brightholdrealty.example</span></p>
    </footer>
  </main>
</body>
</html>
```